Veltmoor Capital Stationary Design

We have selected a logo as our winner, we now need a full stationary set to be in the same theme.
Required:
- Letter Head
- Business Card Template
- Custom Envelopes
- A5 Notepad Design (Front cover and content pages. Content pages blank(no lines) but with our branding on them,)
- With Compliments Slip
Updates

Hey All,

We have changed the colour scheme of our logo. Our apologies if anyone has begun designing based off the old scheme. Please see the updated scheme in the brief,

Oliver

Target Market(s)

Target market is experienced property developers and financial institutions.

Industry/Entity Type

Commercial Finance

Font styles to use
Serif

Colors
0054AA
0677BA
7BADD7
CADEEF
E8F1F8
0094D4
00A9DD
6FCCEA
C7EBF8
E9F6FB
00AB8E
00BBA5
67D7C9
C6EFE9
E9F9F6
59FF00
82FF00
B8FF75
E3FFCB
F4FFEA

```html
<!DOCTYPE html>
<html lang="en">
<head>
<meta charset="utf-8">
<title>Veltmoor Capital – Business Card</title>
<link href="https://fonts.googleapis.com/css2?family=Poppins:wght@400;600&family=Raleway:wght@600;700&display=swap" rel="stylesheet">
<style>
  :root {
    --backdrop: #e2e2e2;
    --card-white: #ffffff;
    --navy: #17366f;
    --brand-blue: #21409a;
    --brand-green: #1f8a3d;
    --ink: #4a4a4a;
  }
  * { box-sizing: border-box; margin: 0; padding: 0; }
  html, body { width: 1173px; height: 1200px; overflow: hidden; }
  body { background: var(--backdrop); position: relative; font-family: "Poppins", sans-serif; }

  .card { position: absolute; left: 204px; width: 743px; height: 411px; }
  .card-front { top: 150px; background: var(--card-white); }
  .card-back { top: 637px; background: var(--navy); }

  .wordmark { position: absolute; font-family: "Poppins", sans-serif; font-weight: 600; white-space: nowrap; }
  .card-front .wordmark { right: 69px; top: 62px; font-size: 31px; color: var(--brand-blue); }
  .card-back .wordmark { left: 0; right: 0; top: 168px; text-align: center; font-size: 54px; color: var(--card-white); }

  .holder-name { position: absolute; left: 71px; top: 204px; font-family: "Raleway", sans-serif; font-weight: 700; font-size: 24px; color: var(--brand-blue); }
  .holder-role { position: absolute; left: 71px; top: 234px; font-family: "Raleway", sans-serif; font-weight: 600; font-size: 17px; color: var(--brand-green); }
  .role-rule { position: absolute; left: 214px; right: 69px; top: 246px; height: 1px; background: var(--brand-green); }

  .contact-list { position: absolute; left: 69px; top: 283px; list-style: none; }
  .contact-list li { display: flex; align-items: center; height: 22.5px; font-size: 17px; color: var(--ink); }
  .contact-list svg { width: 17px; height: 17px; margin-right: 10px; fill: var(--brand-blue); flex: none; }

  .address { position: absolute; right: 69px; top: 305px; text-align: right; font-size: 17px; line-height: 22.5px; color: var(--ink); font-style: normal; }
</style>
</head>
<body>
  <section class="card card-front">
    <div class="wordmark">Veltmoor Capital</div>
    <div class="holder-name">Maren Holloway</div>
    <div class="holder-role">Vice President</div>
    <div class="role-rule"></div>
    <ul class="contact-list">
      <li>
        <svg viewBox="0 0 24 24" aria-hidden="true"><path d="M3 9c0-3 4-5 9-5s9 2 9 5v2h-5V9c-1-.6-2.4-1-4-1s-3 .4-4 1v2H3V9zm4 3h10l2 8H5l2-8zm5 2a2.5 2.5 0 100 5 2.5 2.5 0 000-5z"/></svg>
        (253) 555-0147
      </li>
      <li>
        <svg viewBox="0 0 24 24" aria-hidden="true"><path d="M2 5h20v2l-10 6L2 7V5zm0 4l10 6 10-6v10H2V9z"/></svg>
        maren@veltmoorcapital.com
      </li>
      <li>
        <svg viewBox="0 0 24 24" aria-hidden="true"><path d="M12 2a10 10 0 100 20 10 10 0 000-20zm-1 3c1 1 0 2 1 3s3 0 3 2-2 2-3 3 0 3-1 4-2-1-2-3-2-2-2-4 3-4 4-5zm5 8c1 0 2 1 1 3s-2 2-2 1 0-4 1-4z"/></svg>
        www.veltmoorcapital.com
      </li>
    </ul>
    <address class="address">4127 Larkspur Avenue S<br>Alder Falls, WA 98041</address>
  </section>

  <section class="card card-back">
    <div class="wordmark">Veltmoor Capital</div>
  </section>
</body>
</html>
```